Business card for law firm

Need business card for new law firm. Think confident, authoritative, conservative, but not stuffy or old-fashioned.

Contact Information for Business Card

Content for card - logo (uploaded), plus the following:

Paul Whitcombe (larger font)
Managing Partner (larger font, but not as large as name)
Level 9, 7 Ferris Lane
Sydney NSW 2000
Main Tel 02 9364 2710
Direct Tel 02 8472 3159
Email paul@qvlegal.com.au
www.qvlegal.com.au

Letterhead design should include logo plus:
Level 9, 7 Ferris Lane
Sydney NSW 2000
Tel 02 8472 3159
www.qvlegal.com.au

```html
<!DOCTYPE html>
<html lang="en">
<head>
<meta charset="utf-8">
<title>Quayvale Legal – Business Card</title>
<link href="https://fonts.googleapis.com/css2?family=Montserrat:wght@400;600;700&display=swap" rel="stylesheet">
<style>
  :root {
    --navy: #1f2a5e;
    --ink: #1b1b22;
    --card: #ffffff;
    --backdrop: #e9e9ec;
    --rule: #2a3468;
  }
  * { margin: 0; padding: 0; box-sizing: border-box; }
  html, body {
    width: 1200px;
    height: 900px;
    overflow: hidden;
    background: var(--backdrop);
    font-family: "Montserrat", Arial, sans-serif;
  }
  .canvas {
    width: 1200px;
    height: 900px;
    display: flex;
    align-items: center;
    justify-content: center;
  }
  .business-card {
    position: relative;
    width: 1000px;
    height: 572px;
    background: var(--card);
    box-shadow: 0 10px 30px rgba(0,0,0,0.12);
    display: flex;
    align-items: center;
  }
  .brand {
    width: 500px;
    display: flex;
    align-items: center;
    justify-content: center;
    gap: 18px;
  }
  .brand-mark {
    width: 34px;
    height: 34px;
    background: var(--navy);
  }
  .brand-name {
    font-weight: 600;
    font-size: 40px;
    letter-spacing: 0.06em;
    color: var(--navy);
    text-transform: uppercase;
    white-space: nowrap;
  }
  .divider {
    width: 2px;
    height: 300px;
    background: var(--rule);
  }
  .contact {
    padding-left: 48px;
    color: var(--navy);
  }
  .contact-name {
    font-weight: 700;
    font-size: 34px;
    line-height: 1.1;
  }
  .contact-role {
    font-weight: 400;
    font-size: 26px;
    margin-bottom: 22px;
  }
  .contact-address {
    font-size: 24px;
    line-height: 1.3;
    margin-bottom: 14px;
    font-weight: 600;
  }
  .contact-list { list-style: none; }
  .contact-list li {
    display: flex;
    align-items: center;
    gap: 14px;
    font-size: 24px;
    line-height: 1.35;
    font-weight: 600;
  }
  .contact-list svg {
    width: 18px;
    height: 18px;
    flex: none;
    fill: none;
    stroke: var(--navy);
    stroke-width: 2;
  }
</style>
</head>
<body>
  <main class="canvas">
    <section class="business-card">
      <div class="brand">
        <span class="brand-mark"></span>
        <span class="brand-name">Quayvale Legal</span>
      </div>
      <div class="divider"></div>
      <div class="contact">
        <p class="contact-name">Paul Whitcombe</p>
        <p class="contact-role">Managing Partner</p>
        <p class="contact-address">Level 9, 7 Ferris Lane<br>Sydney NSW 2000</p>
        <ul class="contact-list">
          <li>
            <svg viewBox="0 0 20 20"><path d="M5 2l3 4-2 2c1 2 3 4 5 5l2-2 4 3-2 3C9 17 3 11 2 5z" fill="var(--navy)" stroke="none"/></svg>
            02 9364 2710
          </li>
          <li>
            <svg viewBox="0 0 20 20"><path d="M5 2l3 4-2 2c1 2 3 4 5 5l2-2 4 3-2 3C9 17 3 11 2 5z" fill="var(--navy)" stroke="none"/></svg>
            02 8472 3159
          </li>
          <li>
            <svg viewBox="0 0 20 20"><rect x="2" y="4" width="16" height="12"/><path d="M2 4l8 7 8-7"/></svg>
            paul@qvlegal.com.au
          </li>
          <li>
            <svg viewBox="0 0 20 20"><circle cx="10" cy="10" r="8"/><ellipse cx="10" cy="10" rx="3.5" ry="8"/><path d="M2 10h16M4 5.5h12M4 14.5h12"/></svg>
            www.qvlegal.com.au
          </li>
        </ul>
      </div>
    </section>
  </main>
</body>
</html>
```